"Inkvale" printing shop

-The design must be based around the attached NWPD (home page information design) called "Inkvale - HPID".

The table boxes are just for approximate placement of information – you DON'T have to box everything in and you can arrange these. All fonts used in the NWPD are only examples - you can use any Google font you wish.

- Information only is in orange text. Copy to go on the design in black text. Some instructions are in the NWPD. Please be creative!

-The design needs to be modern. Colours are to be consistent with their new logo or complement it. Keep it clean and simple, you don't need to use lots of colours. Use lots of white.

- images / icons for the site need to be relevant and high quality, but they must also be free images or icons. I have attached a few examples that could be used.

Width of content will be 1100 pixels when implemented as a web page. Header height (without nav bar) 150-200 pixels.

If your design is chosen the winning PSD file will have to be provided as follows…
1. Canvas size of 2000px x 2000px - 72ppi in Adobe Photoshop (CS5 compatible)
2. Width of content section is 1100px wide - centered in the canvas
3. Any button rollovers/hovers in the PSD as hidden layers.
4. All fonts used must be Google fonts.
5. You will need to supply the chosen home page plus one example page (example page as a style guide for how all other pages will look). Example page is only the header and navigational bar at the top, an empty sector in the middle with a column (190 px wide) which can be left or right aligned which means the main sector is 910 pixels wide, and then the footer at the bottom of the page

Checklist - http://pagebuildertally.example/

Examples of some websites that have great design... don't copy them please but they are similar in look to what we are after....
http://www.rookfenly.example/

Industry/Entity Type

Printing

Font styles to use
Serif
Sans Serif

Requirements
Should not have
• Drop shadows, comic sans font

```html
<!DOCTYPE html>
<html lang="en">
<head>
<meta charset="utf-8">
<title>Inkvale - Printing, Laminating and Photocopying</title>
<link rel="stylesheet" href="https://fonts.googleapis.com/css2?family=Lato:ital,wght@0,300;0,400;0,700;0,900;1,300;1,400;1,700&family=Poiret+One&display=swap">
<style>
:root{
  --orange:#ff6600;
  --orange-dark:#a84300;
  --charcoal:#3a3a3a;
  --header:#454545;
  --ink:#333333;
  --mist:#e9ebef;
  --white:#ffffff;
  --rule:#e3e3e3;
}
*{box-sizing:border-box;margin:0;padding:0}
html,body{width:670px;height:1200px;overflow:hidden;background:var(--white);font-family:'Lato',sans-serif;color:var(--ink)}
.page{position:relative;width:670px;height:1200px}

/* header */
.site-header{position:absolute;left:0;top:0;width:670px;height:76px;background:var(--header);border-bottom:2px dotted #777}
.brand{position:absolute;left:70px;top:16px;display:flex;align-items:center;gap:6px;color:var(--white);font-weight:900;font-size:24px;letter-spacing:-.3px}
.brand-mark{width:32px;height:32px;border-radius:50%;background:var(--white)}
.tagline{position:absolute;left:184px;top:18px;color:var(--white)}
.tagline h1{font-weight:400;font-size:17.5px;letter-spacing:.2px}
.tagline p{font-size:10px;margin-top:4px}
.contact{position:absolute;left:530px;top:12px;color:var(--white);font-size:5.6px;line-height:9px}
.contact div{display:flex;gap:5px;align-items:flex-start}
.contact svg{flex:none;margin-top:1px}

/* nav */
.main-nav,.foot-nav{position:absolute;left:0;width:670px;text-align:center;font-size:5.6px;white-space:nowrap}
.main-nav{top:93px;font-style:italic;color:#222}
.main-nav span,.foot-nav span{padding:0 3px}
.hero-rule{position:absolute;left:0;width:670px;height:1px;background:#f5a46b}

/* hero */
.hero-title{position:absolute;left:70px;top:164px;font-weight:300;font-style:italic;font-size:20px;line-height:24.5px;color:#444}
.btn{position:absolute;display:flex;align-items:center;justify-content:center;background:var(--orange);color:var(--white);font-weight:700;border-radius:12px}
.btn-hero{left:70px;top:276px;width:83px;height:25px;font-size:7.5px}
.hero-visual{position:absolute;left:276px;top:141px;width:380px;height:190px;border-radius:4px;background:linear-gradient(180deg,#c9cdd2 0%,#c9cdd2 14%,#5d7a2a 30%,#9bbd3c 70%,#6f8f22 100%)}

/* services */
.services{position:absolute;left:0;top:350px;width:670px;height:327px;background:var(--mist)}
.card{position:absolute;width:167px;height:127px;background:var(--orange);color:var(--white)}
.card::before{content:"";position:absolute;right:0;top:0;width:25px;height:25px;background:linear-gradient(225deg,var(--mist) 50%,var(--orange-dark) 50%)}
.card h3{position:absolute;left:10px;top:28px;display:flex;align-items:center;gap:8px;font-weight:700;font-style:italic;font-size:10px}
.card p{position:absolute;left:9px;top:58px;width:132px;font-size:6.3px;line-height:7px;text-align:justify}
.card .more{position:absolute;left:9px;top:95px;font-weight:700;font-size:7.5px}

/* features */
.feature{position:absolute;width:258px;height:57px;border-bottom:1px solid var(--rule)}
.feature .num{position:absolute;left:0;top:0;width:32px;height:32px;border-radius:50%;background:var(--orange);color:var(--white);font-weight:700;font-size:18px;display:flex;align-items:center;justify-content:center}
.feature h4{position:absolute;left:38px;top:0;color:var(--orange);font-size:9.6px;font-weight:700}
.feature p{position:absolute;left:38px;top:16px;width:222px;font-size:6.2px;line-height:7.5px}
.feature .more{position:absolute;left:38px;top:37px;color:var(--orange);font-size:7px;font-weight:700;letter-spacing:.3px}

/* quote */
.quote{position:absolute;left:0;top:904px;width:670px;height:229px;background:var(--charcoal);color:var(--white)}
.quote h2{position:absolute;top:17px;font-family:'Poiret One',sans-serif;font-weight:400;font-size:16px;letter-spacing:.3px}
.quote .intro{position:absolute;left:70px;top:51px;width:213px;font-size:9.6px;line-height:10px;text-align:justify}
.social{position:absolute;top:143px;width:27px;height:27px;border-radius:50%;background:var(--orange)}
.field{position:absolute;border:1px solid #cfcfcf;font-size:6.4px;padding:5px 5px;color:#eee}
.btn-send{left:422px;top:153px;width:59px;height:18px;font-size:7px;border-radius:9px}

.foot-nav{top:1133px;height:35px;line-height:35px;background:var(--orange);color:var(--white)}
.copyright{position:absolute;left:0;top:1168px;width:670px;height:32px;background:#3c3c3c;color:#aaa;font-size:7px;text-align:center;line-height:32px}
</style>
</head>
<body>
<div class="page">

  <header class="site-header">
    <div class="brand"><span class="brand-mark"></span>Inkvale</div>
    <div class="tagline">
      <h1>Duplication is our vocation</h1>
      <p>Professional photocopying - digital &amp; film processing, design and printing</p>
    </div>
    <div class="contact">
      <div><svg width="5" height="7" viewBox="0 0 5 7"><rect x=".5" y=".5" width="4" height="6" rx=".8" fill="none" stroke="#fff"/></svg>07 555 0148</div>
      <div style="margin-top:3px"><svg width="5" height="7" viewBox="0 0 5 7"><path d="M2.5 7C1 4.8 0 3.6 0 2.5a2.5 2.5 0 0 1 5 0C5 3.6 4 4.8 2.5 7z" fill="#fff"/></svg><span>12/88 Harbour Lane -<br>Westfield - Kelmora</span></div>
    </div>
  </header>

  <nav class="main-nav"><span>Home</span>|<span>About</span>|<span>Photocopying</span>|<span>Printing</span>|<span>Laminating</span>|<span>Business cards</span>|<span>Typing services</span>|<span>Film processing</span>|<span>Photo Printing</span>|<span>Passport photos</span>|<span>Image Restoration</span>|<span>Printer Supplies</span>|<span>Free quote</span>|<span>Contact</span></nav>
  <div class="hero-rule" style="top:118px"></div>

  <section>
    <h2 class="hero-title">Digital printing,<br>Laminating and<br>Photocopying services<br>Throughout Kelmora</h2>
    <a class="btn btn-hero">READ MORE</a>
    <div class="hero-visual" role="img" aria-label="Wide-format printer producing a photo print of a small figure on grass with bubbles"></div>
  </section>
  <div class="hero-rule" style="top:349px"></div>

  <section class="services">
    <article class="card" style="left:70px;top:33px">
      <h3><svg width="26" height="18" viewBox="0 0 26 18" fill="none" stroke="#fff" stroke-width="1.6"><path d="M13 2 24 7 13 12 2 7z"/><path d="M2 10l11 5 11-5"/></svg>Photocopyin</h3>
      <p>Aenean aucto. wisi et urna. Aliqat tpat. Duisac turpis. Integer rutrumante eu lacuestibulm libero nisl porta vel sceleriget malesuadt eget nibh.</p>
      <span class="more">READ MORE &#10230;</span>
    </article>
    <article class="card" style="left:251px;top:33px">
      <h3><svg width="22" height="20" viewBox="0 0 22 20" fill="none" stroke="#fff" stroke-width="1.6"><rect x="5" y="1" width="12" height="7"/><rect x="1" y="8" width="20" height="8"/><path d="M5 13h12"/></svg>Laminating &amp; Binding</h3>
      <p>Aenean aucto. wisi et urna. Aliqat tpat. Duisac turpis. Integer rutrumante eu lacuestibulm libero nisl porta vel sceleriget malesuadt eget nibh.</p>
      <span class="more">READ MORE &#10230;</span>
    </article>
    <article class="card" style="left:434px;top:33px">
      <h3><svg width="20" height="20" viewBox="0 0 20 20" fill="none" stroke="#fff" stroke-width="1.6"><rect x="4" y="1" width="12" height="8"/><rect x="1" y="9" width="18" height="8"/><path d="M7 4h6M7 6h6"/></svg>Digital Printin</h3>
      <p>Aenean aucto. wisi et urna. Aliqat tpat. Duisac turpis. Integer rutrumante eu lacuestibulm libero nisl porta vel sceleriget malesuadt eget nibh.</p>
      <span class="more">READ MORE &#10230;</span>
    </article>
    <article class="card" style="left:70px;top:175px">
      <h3><svg width="22" height="22" viewBox="0 0 22 22"><circle cx="11" cy="11" r="10" fill="#fff"/><circle cx="11" cy="6" r="3" fill="#ff6600"/><circle cx="6.5" cy="14" r="3" fill="#ff6600"/><circle cx="15.5" cy="14" r="3" fill="#ff6600"/></svg>Film Processing</h3>
      <p>Aenean aucto. wisi et urna. Aliqat tpat. Duisac turpis. Integer rutrumante eu lacuestibulm libero nisl porta vel sceleriget malesuadt eget nibh.</p>
      <span class="more">READ MORE &#10230;</span>
    </article>
    <article class="card" style="left:251px;top:175px">
      <h3><svg width="26" height="18" viewBox="0 0 26 18" fill="none" stroke="#fff" stroke-width="1.6"><rect x="1" y="1" width="24" height="16" rx="2"/><path d="M5 7h6M5 11h6"/><circle cx="18" cy="7" r="2"/><path d="M14 13c1-3 7-3 8 0"/></svg>Business Card</h3>
      <p>Aenean aucto. wisi et urna. Aliqat tpat. Duisac turpis. Integer rutrumante eu lacuestibulm libero nisl porta vel sceleriget malesuadt eget nibh.</p>
      <span class="more">READ MORE &#10230;</span>
    </article>
    <article class="card" style="left:434px;top:175px">
      <h3><svg width="22" height="22" viewBox="0 0 22 22" fill="none" stroke="#fff" stroke-width="1.6"><rect x="5" y="1" width="12" height="6"/><rect x="1" y="7" width="20" height="8"/><rect x="6" y="12" width="10" height="9" fill="#ff6600"/></svg>Photo Printing</h3>
      <p>Aenean aucto. wisi et urna. Aliqat tpat. Duisac turpis. Integer rutrumante eu lacuestibulm libero nisl porta vel sceleriget malesuadt eget nibh.</p>
      <span class="more">READ MORE &#10230;</span>
    </article>
  </section>

  <section class="features">
    <div class="feature" style="left:70px;top:701px"><span class="num">1</span><h4>Cost effective photocopying</h4><p>No matter the quantity of photocopies you need or the size of your copy - you can rely on us to provide a top quality service!</p><span class="more">MORE INFO &#10150;</span></div>
    <div class="feature" style="left:342px;top:701px"><span class="num">2</span><h4>Personal desktop publishing</h4><p>From personalised brochures, posters and birthday and special occasion cards to top quality, cheap business cards - you get it all!</p><span class="more">MORE INFO &#10150;</span></div>
    <div class="feature" style="left:70px;top:767px"><span class="num">3</span><h4>All digital format printing</h4><p>Either email us your file or bring it into the store and we can get you the print you need. All prints are to the highest quality.</p><span class="more">MORE INFO &#10150;</span></div>
    <div class="feature" style="left:342px;top:767px"><span class="num">4</span><h4>Film photo processing</h4><p>Bring in your film to the store and we will work with you to get the best quality print for your purpose and needs. We work with it all!</p><span class="more">MORE INFO &#10150;</span></div>
    <div class="feature" style="left:70px;top:833px"><span class="num">5</span><h4>Laminating and binding</h4><p>Create a professional image for your documents or books. Lamination and binding also keeps your documents well protected!</p><span class="more">MORE INFO &#10150;</span></div>
    <div class="feature" style="left:342px;top:833px"><span class="num">6</span><h4>Quality digital photo prints</h4><p>Get your photo printed to your requirements - either from a file or from your digital camera. With a wide range of options you can get the print you want.</p><span class="more">MORE INFO &#10150;</span></div>
  </section>

  <section class="quote">
    <h2 style="left:70px">Get a free quote</h2>
    <div class="intro"><p>...or talk to our team about your requirements. Please fill out the form below and we will contact you within a day.</p><p style="margin-top:9px">You can now upload and send us your file for a free quote!</p></div>
    <span class="social" style="left:70px"></span>
    <span class="social" style="left:107px"></span>
    <span class="social" style="left:145px"></span>
    <span class="social" style="left:182px"></span>
    <span class="social" style="left:218px"></span>
    <span class="social" style="left:255px"></span>

    <h2 style="left:297px">Equire Form</h2>
    <div class="field" style="left:297px;top:50px;width:149px;height:19px">First Name</div>
    <div class="field" style="left:452px;top:50px;width:149px;height:19px">Last Name</div>
    <div class="field" style="left:297px;top:73px;width:149px;height:19px">Number</div>
    <div class="field" style="left:452px;top:73px;width:149px;height:19px">Email</div>
    <div class="field" style="left:297px;top:97px;width:304px;height:51px">Message</div>
    <a class="btn btn-send">SEND</a>
  </section>

  <nav class="foot-nav"><span>Home</span>|<span>About</span>|<span>Photocopying</span>|<span>Printing</span>|<span>Laminating</span>|<span>Business cards</span>|<span>Typing services</span>|<span>Film processing</span>|<span>Photo Printing</span>|<span>Passport photos</span>|<span>Image Restoration</span>|<span>Printer Supplies</span>|<span>Free quote</span>|<span>Contact</span></nav>
  <footer class="copyright">Inkvale - NWPD &copy; copyright 2015 &bull; Privacy Policy</footer>

</div>
</body>
</html>
```